Business Card for Beach theme sports bar called MORVIN

I need a business card designed for our employees, front and back. This will be used by the employees of two business locations to hand out to customers. I've attached the previous business cards we used at one time for a Dantells (it is now Morvin). Looking for a fresh new card that is elegant but has character.

Target Market(s)

30-60, middle class

Contact Information for Business Card

We are a beach bar and sports bar. I am looking for an elegant business card with the front to have the MORVIN logo. Then on the back I need it to allow a space for employees to write their names and for them to write in their schedule. I have attached our old cards with our old name Dantells so you can pull everything we need on the cards. one thing is missing is we have another location at 2615 W Calder Ridge Rd with a number of 702-418-9053. Since we will use it for both locations it should allow the employee to circle or check mark the bar which they work at.

Font styles to use
Sans Serif

Requirements
Must have
• We are looking for some fresh ideas for the business card. Something that will really stick out to customers when the staff hands them out. Creativity will be looked at positively, but we still want it to look upscale and fun.

```html
<!DOCTYPE html>
<html lang="en">
<head>
<meta charset="utf-8">
<title>Morvin – Business Cards</title>
<link href="https://fonts.googleapis.com/css2?family=Barlow:wght@400;500;700&display=swap" rel="stylesheet">
<style>
  :root {
    --sun: #f5c75e;
    --sun-pale: #fbefd2;
    --mint: #bfe3d8;
    --mint-pale: #e6f4ef;
    --ink: #1d1d1b;
    --paper: #ffffff;
    --rule: #a8a8a8;
  }
  * { box-sizing: border-box; margin: 0; padding: 0; }
  html, body { width: 850px; height: 1200px; overflow: hidden; background: var(--paper); }
  body { font-family: "Barlow", sans-serif; color: var(--ink); position: relative; }

  .sheet-title {
    position: absolute; top: 34px; left: 0; width: 850px;
    text-align: center; font-weight: 400; font-size: 27px; line-height: 32px;
  }
  .card { position: absolute; width: 370px; height: 220px; overflow: hidden; }
  .card--left { left: 45px; }
  .card--right { left: 435px; }
  .row-front { top: 104px; }
  .row-back { top: 360px; }

  .front { display: flex; align-items: center; justify-content: center; gap: 12px; }
  .front--sun { background: var(--sun); }
  .front--mint { background: var(--mint); }
  .brand-dot { width: 16px; height: 16px; border-radius: 50%; background: var(--ink); }
  .brand-name { font-weight: 700; font-size: 54px; letter-spacing: 1px; color: var(--ink); }

  .role-label {
    position: absolute; top: 342px; left: 68px;
    font-weight: 700; font-size: 14px; letter-spacing: .3px;
  }

  .back { background: var(--paper); border: 1px solid var(--rule); }
  .back-decor { position: absolute; right: 0; bottom: 0; width: 70px; height: 120px;
    border-radius: 60px 0 0 0; }
  .back--sun .back-decor { background: var(--sun-pale); }
  .back--mint .back-decor { background: var(--mint-pale); }

  .name-band { position: absolute; top: 16px; left: 14px; width: 340px; height: 46px; border-radius: 23px; }
  .back--sun .name-band { background: var(--sun); }
  .name-field { position: absolute; top: 9px; left: 128px; width: 174px; height: 28px; background: var(--paper); }

  .back--mint .name-band { background: var(--mint); border-radius: 20px 20px 8px 20px; }
  .band-notch { position: absolute; top: 35px; left: 113px; width: 215px; height: 11px; background: var(--paper); }
  .band-title { position: absolute; top: 12px; left: 22px; font-weight: 700; font-size: 14px; }

  .schedule { position: absolute; top: 78px; left: 58px; display: flex; gap: 7px; }
  .day { width: 27px; text-align: center; position: relative; }
  .day-name { font-size: 13px; height: 18px; line-height: 18px; }
  .day-box { width: 27px; height: 23px; margin-top: 3px; border: 1.5px solid var(--sun); }
  .back--mint .day-box { border-color: var(--mint); }
  .mark { position: absolute; pointer-events: none; }
  .mark line { stroke: var(--ink); stroke-width: 1.2; stroke-linecap: round; }

  .location { position: absolute; text-align: center; font-size: 8.3px; line-height: 10.5px; width: 140px; font-style: normal; }
  .loc-a { left: 34px; top: 164px; }
  .loc-b { left: 196px; top: 164px; }
  .back--mint .loc-a { top: 162px; }
  .back--mint .loc-b { top: 172px; }
</style>
</head>
<body>
  <h1 class="sheet-title">Business Cards<br>3,4 x 2 in</h1>

  <section class="card card--left row-front front front--sun" aria-label="Card front, sun yellow">
    <span class="brand-dot"></span><span class="brand-name">Morvin</span>
  </section>
  <section class="card card--right row-front front front--mint" aria-label="Card front, mint">
    <span class="brand-dot"></span><span class="brand-name">Morvin</span>
  </section>

  <p class="role-label">BARTENDER</p>

  <section class="card card--left row-back back back--sun" aria-label="Card back with name field">
    <div class="back-decor" role="img" aria-label="Faint palm leaf decoration"></div>
    <div class="name-band">
      <div class="name-field" role="img" aria-label="Handwritten employee name"></div>
    </div>
    <div class="schedule">
      <div class="day"><div class="day-name">M</div><div class="day-box"></div>
        <svg class="mark" style="left:6px;top:1px" width="15" height="16" aria-hidden="true"><line x1="2" y1="2" x2="13" y2="14"/><line x1="13" y1="2" x2="2" y2="14"/></svg></div>
      <div class="day"><div class="day-name">T</div><div class="day-box"></div></div>
      <div class="day"><div class="day-name">W</div><div class="day-box"></div></div>
      <div class="day"><div class="day-name">Th</div><div class="day-box"></div></div>
      <div class="day"><div class="day-name">F</div><div class="day-box"></div></div>
      <div class="day"><div class="day-name">Sa</div><div class="day-box"></div></div>
      <div class="day"><div class="day-name">Su</div><div class="day-box"></div></div>
    </div>
    <svg class="mark" style="left:258px;top:140px" width="16" height="18" aria-hidden="true"><line x1="2" y1="2" x2="14" y2="16"/><line x1="14" y1="2" x2="2" y2="16"/></svg>
    <address class="location loc-a">3380 W Halden Park Rd<br>Las Vegas, NV 89146<br>702-536-7214<br>hello@morvinbar.com</address>
    <address class="location loc-b">2615 W Calder Ridge Rd<br>Las Vegas, NV 89147<br>702-418-9053<br>hello@morvinbar.com</address>
  </section>

  <section class="card card--right row-back back back--mint" aria-label="Card back with role band">
    <div class="back-decor" role="img" aria-label="Faint palm leaf decoration"></div>
    <div class="name-band">
      <span class="band-title">BARTENDER</span>
      <div class="band-notch"></div>
    </div>
    <div class="schedule">
      <div class="day"><div class="day-name">M</div><div class="day-box"></div></div>
      <div class="day"><div class="day-name">T</div><div class="day-box"></div></div>
      <div class="day"><div class="day-name">W</div><div class="day-box"></div></div>
      <div class="day"><div class="day-name">Th</div><div class="day-box"></div></div>
      <div class="day"><div class="day-name">F</div><div class="day-box"></div></div>
      <div class="day"><div class="day-name">Sa</div><div class="day-box"></div></div>
      <div class="day"><div class="day-name">Su</div><div class="day-box"></div></div>
    </div>
    <address class="location loc-a">3380 W Halden Park Rd<br>Las Vegas, NV 89146<br>702-536-7214<br>hello@morvinbar.com</address>
    <address class="location loc-b">2615 W Calder Ridge Rd<br>Las Vegas, NV 89147<br>702-418-9053<br>hello@morvinbar.com</address>
  </section>
</body>
</html>
```